Business card for Eyelash extension salon in Beverly Hills,California USA

We need new business card for our salon in Beverly Hills. The salon name is 'Lashvera' . We would like to have...Business name: Lashvera Name of person: will provide later Address 4720 N.Alder Crest Ave Beverly Hills , CA 90210 Phone: will provide later (Text only) Web: www.lashverastudio.example Snapgrid icon, Circlebook icon follow us for seasonal campaign and news @lashverastudiolounge Design should look elegant, high-end, clean, simple, cohesive with my brand. Please refer my brand board. Business name color will be metallic bronzy color. Im thinking grey background or white background. Thanks

Target Market(s)

25-35. Gender neutral. People who are in Entertainment business industry.
This is High-end Eyelash extension salon in Beverly Hills

Industry/Entity Type

Beauty Salon

Contact Information for Business Card

Business name: Lashvera
Name of person: will provide later
Address 4720 N.Alder Crest Ave Beverly Hills , CA 90210
Phone: will provide later (Text only)
Web: www.lashverastudio.example
Snapgrid icon, Circlebook icon
follow us for seasonal campaign and news @lashverastudiolounge

Requirements
Must have
• Beautiful, elegant, clean and simple look but very attractive and modern
Should not have
• We don't like too clutter, too busy designs.

```html
<!DOCTYPE html>
<html lang="en">
<head>
<meta charset="utf-8">
<title>Lashvera Beverly Hills – Business Card</title>
<link rel="stylesheet" href="https://fonts.googleapis.com/css2?family=Open+Sans:wght@300;400;600&family=Arimo:wght@700&display=swap">
<style>
  :root {
    --stage: #161616;
    --card: #232323;
    --card-edge: #2c2c2c;
    --rule: #4a4a4a;
    --bronze: #a87a5c;
    --silver: #c9c9c9;
    --text: #f2f2f2;
    --muted: #8a8a8a;
  }
  * { box-sizing: border-box; margin: 0; padding: 0; }
  html, body {
    width: 1200px; height: 900px; overflow: hidden;
    background: var(--stage);
    font-family: "Open Sans", Arial, sans-serif;
    color: var(--text);
  }
  .stage {
    width: 1200px; height: 900px;
    display: flex; flex-direction: column; align-items: center; justify-content: center;
    gap: 40px;
  }
  .card {
    position: relative;
    width: 640px; height: 366px;
    background: var(--card);
    border: 1px solid var(--card-edge);
    border-radius: 24px;
    overflow: hidden;
  }

  /* Brand wordmark */
  .wordmark { position: absolute; text-align: right; }
  .wordmark__name {
    display: block;
    font-weight: 300;
    font-size: 64px;
    line-height: 1;
    letter-spacing: 1px;
  }
  .wordmark__place {
    display: block;
    margin-top: 6px;
    font-size: 8px;
    letter-spacing: 3px;
    text-transform: uppercase;
  }

  /* Social side */
  .card--social .wordmark { left: 0; right: 0; top: 62px; text-align: center; }
  .card--social .wordmark__name { color: var(--silver); }
  .card--social .wordmark__place { color: var(--muted); margin-left: 150px; }
  .card--social .rule { position: absolute; left: 40px; right: 40px; height: 1px; background: var(--rule); }
  .card--social .rule--top { top: 178px; }
  .card--social .rule--bottom { top: 292px; }
  .social-links {
    position: absolute; top: 196px; left: 0; right: 0;
    display: flex; justify-content: center; gap: 22px;
    font-size: 12px; font-weight: 600; color: var(--text);
  }
  .social-links__item { display: flex; align-items: center; gap: 7px; }
  .social-links__dot { width: 14px; height: 14px; border-radius: 50%; background: var(--text); }
  .follow-line {
    position: absolute; top: 244px; left: 0; right: 0;
    text-align: center; font-size: 14px; color: var(--text);
  }

  /* Contact side */
  .card--contact .wordmark { right: 56px; top: 50px; }
  .card--contact .wordmark__name { color: var(--bronze); }
  .card--contact .wordmark__place { color: var(--bronze); opacity: .8; }
  .card--contact .rule--head {
    position: absolute; top: 150px; left: 250px; right: 40px; height: 1px; background: var(--rule);
  }
  .address {
    position: absolute; top: 172px; right: 40px;
    text-align: right; font-size: 15px; line-height: 1.4; color: var(--text);
  }
  .holder {
    position: absolute; left: 40px; right: 40px; top: 250px;
    display: flex; align-items: center; gap: 14px;
  }
  .holder__name {
    font-family: "Arimo", Arial, sans-serif;
    font-weight: 700; font-size: 19px; letter-spacing: .5px;
    color: var(--bronze); text-transform: uppercase; white-space: nowrap;
  }
  .holder__rule { flex: 1; height: 1px; background: var(--rule); }
  .contact-list {
    position: absolute; left: 40px; top: 286px;
    list-style: none; font-size: 15px; line-height: 1.55;
  }
  .contact-list__item { display: flex; align-items: center; gap: 8px; }
  .contact-list__icon { width: 13px; height: 13px; fill: var(--bronze); flex: none; }
</style>
</head>
<body>
<main class="stage">

  <section class="card card--social" aria-label="Business card, social side">
    <div class="wordmark">
      <span class="wordmark__name">Lashvera</span>
      <span class="wordmark__place">Beverly Hills</span>
    </div>
    <div class="rule rule--top"></div>
    <div class="social-links">
      <span class="social-links__item"><span class="social-links__dot"></span>Circlebook</span>
      <span class="social-links__item"><span class="social-links__dot"></span>Snapgrid</span>
    </div>
    <p class="follow-line">Follow us for seasonal campaign and news @lashverastudiolounge</p>
    <div class="rule rule--bottom"></div>
  </section>

  <section class="card card--contact" aria-label="Business card, contact side">
    <div class="wordmark">
      <span class="wordmark__name">Lashvera</span>
      <span class="wordmark__place">Beverly Hills</span>
    </div>
    <div class="rule--head"></div>
    <address class="address" style="font-style:normal">
      4720 N.Alder Crest Ave<br>Beverly Hills , CA 90210
    </address>
    <div class="holder">
      <span class="holder__name">Marcus Delray</span>
      <span class="holder__rule"></span>
    </div>
    <ul class="contact-list">
      <li class="contact-list__item">
        <svg class="contact-list__icon" viewBox="0 0 16 16" aria-hidden="true">
          <path d="M1 5c0-2 2-3 7-3s7 1 7 3v1h-3.5V4.5h-7V6H1z"/>
          <path d="M4 7.5 5.5 6h5L12 7.5 14 13H2z"/>
        </svg>
        055-284 619 302
      </li>
      <li class="contact-list__item">
        <svg class="contact-list__icon" viewBox="0 0 16 16" aria-hidden="true">
          <circle cx="8" cy="8" r="7"/>
          <path d="M1 8h14M8 1c-3 3-3 11 0 14M8 1c3 3 3 11 0 14" stroke="#232323" stroke-width="1.1" fill="none"/>
        </svg>
        www.lashverastudio.example
      </li>
    </ul>
  </section>

</main>
</body>
</html>
```